TalkSift Website Re-skin

TalkSift.com needs to be re-skinned. The form design of the website and talksift logo are is to stay as-is. The images, type font and background color need to be updated to attempt to achieve a professionally-progressive first impression. We are also amiable to any recommended copy changes, but the main focus of this initiative is to replace the tired and muted existing images, background, and type font. I have included a number of websites that have the look and feel that we would like to inspire the refresh.... These websites also do a good job to include images that blend a computer, ipad, or iphone with a somewhat blurred background.

I included two company overview documents to describe the service. You can also log into the site and receive 5 Free interviews so that you can experience the site yourself in about 10 minutes.

Another high level overview is described in this video link:
http://clipmarsh.example/q7Lr2-Xpdwe
Updates

We received some questions from a few designers and I want to make sure that I share my responses with everyone.  

How many pages do we want:  
We would like 3 pages.  The Home Page, the Login Page, and the Create Account Page.  Note: The large majority of the work should be focused on the Home Page.  The Login and Create Account pages just need to have the background and overall theme from the Home Page design.  

Is coding a must for the Project:  
Coding is highly preferred as it will help reduce the process of splicing up the artwork files.  As such, our preference is to obtain the coding with the project. 

What type of Coding do we want?
HTML/CSS is acceptable

Note:  I also added some Logo .png files onto the craft yard site

Target Market(s)

Please refer to the attached "company description" and "business overview" documents. General target audience is small, medium and large organizations seeking to reduce the time and cost to interview qualified job candidates. Given that TalkSift serves small to large organizations, we would like our design to error on the size of "professionally progressive" such that it has the visual appearance of being sophisticated and technologically sound.

Industry/Entity Type

Computer

Requirements
Must have
• Seeking to have 3 pages re-skinned. The Home Page, the Login Page, and the Create Account Page. Note. The Login and Create Account Pages should be very straight forward with limited work required as we seek little design change for them and would like them to carry over the theme and colors from the Home Page. Hence, re-skinning the home page with the elements described below is the major focus.

Top of Home Page: Replace main image of lady coming out of resume/ipad screen with an image very similar to the one on the attached file titled "plinko home page lady" Note: Plinko changed its name to Brisel so duplicating this approach is okay to mimic this image without issue. We especially like this image as it is colorful and visually describes the service we provide.

The layout of the "Oru iPad" and "Telvo Home page i-pad" files that are attached are nice. There may be a way to leverage the plinko lady with the Oru Ipad image to make a nice visual.

Verbiage: Change copy from "Welcome to Talksift! Talksift is your fully automated interviewing solution. Personalized to your brand, you will save time and money selecting the best candidates" To Now Read: "Humanize and accelerate your interview screening process with TalkSift."

Background: We really like the way that Oru changes their back-grounds as the themes/subjects change when scrolling down their main web page. Achieving this sort of experience would be ideal. It is also acceptable to have a more contrasting background color that may be darker. If this is done, then the words could be in white. This is not a requirement, just some general direction.

Font type: We like the font type from Oru (see attached file titled "Oru iPad")

Font Color: Okay to change font from the dull blue that we have today and use a different more contrasting or popping color.

We like outlining steps 1 through 4 but prefer to replace the people holding the placards with some other images that are potentially in a family of images that all tie together.

It is okay to keep the images in the "Responsive Layout" section of the site (located about 3/4ths of the way down the page) as these seem to be more current and do a good job to illustrate images with an ipad or computer.

Benefits Section: Prefer to change this section. Listing nine (9) separate benefits are too many to make any impact. Advocate illustrating the following benefits:
- "Reduce time and cost to screen candidates"
- "Design site with your logo and colors"
- "Customize interview questions for all your postings"
- "Interview candidates anywhere in the world"
- "Review candidate video's anytime / anywhere"

Nice to have
• Potential to add an image whereby it shows / illustrates talksift's administrative portal "talksift admin portal" (attached) to an image of an ipad screen similar to how the attached images for the following websites: "Telvo" "WeareHalcyon" and "marshbell"

```html
<!DOCTYPE html>
<html lang="en">
<head>
<meta charset="utf-8">
<title>TalkSift – Create an Account</title>
<link href="https://fonts.googleapis.com/css2?family=Roboto:ital,wght@0,300;0,400;0,500;1,300&display=swap" rel="stylesheet">
<style>
  :root {
    --brand-blue: #175e9e;
    --title-blue: #1d62a3;
    --footer-blue: #079fdf;
    --nav-top: #ffffff;
    --nav-bottom: #dcdcdc;
    --field-border: #d6d6d6;
    --placeholder: #a6a6a6;
    --text-dark: #2b2b2b;
    --help-yellow: #f1cf7f;
    --link-blue: #1a3cf0;
    --white: #ffffff;
  }
  * { box-sizing: border-box; margin: 0; padding: 0; }
  html, body { width: 1200px; height: 922px; overflow: hidden; }
  body { position: relative; font-family: "Roboto", Arial, sans-serif; background: var(--white); color: var(--text-dark); }

  .site-header { position: absolute; left: 0; top: 0; width: 1200px; height: 97px; background: var(--brand-blue); }
  .brand { position: absolute; left: 105px; top: 12px; display: flex; align-items: center; gap: 10px; }
  .brand-mark { width: 64px; height: 64px; border-radius: 50%; background: #3aa7e8; }
  .brand-name { color: var(--white); font-size: 22px; font-weight: 400; letter-spacing: 1px; line-height: 1; }
  .brand-tagline { color: var(--white); font-size: 11px; letter-spacing: 2px; text-transform: uppercase; margin-top: 4px; font-weight: 400; }
  .header-button { position: absolute; top: 36px; height: 28px; border-radius: 4px; background: linear-gradient(#ffffff, #d9d9d9);
    color: #222; font-size: 15px; line-height: 28px; text-align: center; }
  .header-button.login { left: 833px; width: 80px; }
  .header-button.signup { left: 923px; width: 122px; }

  .main-nav { position: absolute; left: 0; top: 97px; width: 1200px; height: 45px; background: linear-gradient(var(--nav-top), var(--nav-bottom)); }
  .nav-tab { position: absolute; top: 0; height: 45px; line-height: 45px; font-size: 15px; color: #555; }
  .nav-tab.active { left: 101px; width: 94px; background: var(--brand-blue); color: var(--white); text-align: center; }
  .nav-tab.pricing { left: 207px; }

  .page-title { position: absolute; left: 109px; top: 174px; font-size: 32px; font-weight: 300; color: var(--title-blue); }
  .section-title { position: absolute; top: 226px; font-size: 20px; font-weight: 300; color: #222; }
  .section-title.personal { left: 109px; }
  .section-title.company { left: 650px; }

  .help-dot { position: absolute; width: 16px; height: 16px; border-radius: 50%; background: var(--help-yellow);
    border: 1px solid #c9a24e; font-size: 10px; font-weight: 500; text-align: center; line-height: 14px; color: #333; }

  .field { position: absolute; width: 305px; height: 42px; border: 1px solid var(--field-border); border-radius: 8px;
    font-size: 15px; font-style: italic; font-weight: 300; color: var(--placeholder); line-height: 40px; padding-left: 15px; }
  .col-left { left: 110px; }
  .col-right { left: 649px; }

  .captcha { position: absolute; left: 111px; top: 523px; width: 464px; height: 113px; border: 1px solid #ddd; }
  .captcha-images { position: absolute; left: 10px; top: 7px; width: 302px; height: 58px; border: 1px solid #ccc; }
  .captcha-word { position: absolute; left: 6px; top: 4px; width: 132px; height: 48px; background: linear-gradient(90deg, #ececec, #d0d0d0); }
  .captcha-photo { position: absolute; left: 146px; top: 2px; width: 144px; height: 54px; background: linear-gradient(#2c3127, #6b6e62, #3a3d33); }
  .captcha-controls { position: absolute; left: 331px; top: 14px; display: flex; flex-direction: column; gap: 2px; }
  .captcha-controls span { display: block; width: 24px; height: 14px; background: #2a6dc4; border-radius: 2px; }
  .captcha-badge { position: absolute; left: 374px; top: 18px; display: flex; align-items: center; gap: 4px; color: #b5b5b5; font-size: 10px; font-weight: 500; }
  .captcha-badge i { display: block; width: 22px; height: 22px; border-radius: 50%; border: 3px solid #c4c4c4; }
  .captcha-input { position: absolute; left: 7px; top: 74px; width: 317px; height: 30px; border: 1px solid #333; border-radius: 3px;
    font-size: 14px; color: #888; padding-left: 7px; line-height: 28px; }
  .captcha-link { position: absolute; left: 324px; top: 80px; font-size: 18px; color: var(--link-blue); }

  .state-label { position: absolute; left: 655px; top: 484px; font-size: 16px; font-style: italic; font-weight: 300; color: #888; }
  .state-select { position: absolute; left: 705px; top: 472px; width: 72px; height: 42px; border: 1px solid var(--field-border); border-radius: 8px;
    font-size: 15px; font-style: italic; font-weight: 300; color: var(--placeholder); padding-left: 12px; line-height: 40px; }
  .state-select svg { position: absolute; right: 6px; top: 13px; }

  .submit-button { position: absolute; left: 652px; top: 686px; width: 167px; height: 44px; background: var(--brand-blue);
    color: var(--white); font-size: 17px; font-weight: 300; line-height: 44px; text-align: center; }

  .site-footer { position: absolute; left: 0; top: 765px; width: 1200px; height: 157px; background: var(--footer-blue); color: var(--white); }
  .footer-heading { position: absolute; top: 20px; font-size: 15px; font-weight: 400; }
  .footer-value { left: 109px; }
  .footer-value p { position: absolute; top: 28px; left: 0; width: 460px; font-size: 15px; font-weight: 300; line-height: 24px; color: #e6f5fc; }
  .footer-contact { left: 616px; }
  .footer-contact ul { list-style: none; position: absolute; top: 28px; left: 3px; width: 170px; font-size: 15px; font-weight: 300; line-height: 24px; color: #e6f5fc; }
  .footer-follow { left: 986px; }
  .footer-divider { position: absolute; top: 28px; width: 2px; height: 117px; background: #d9f0fb; }
  .social-links { position: absolute; left: 984px; top: 54px; display: flex; gap: 6px; }
  .social-links span { width: 25px; height: 25px; border-radius: 3px; background: #1f66b0; border: 1px solid #0d4f92; }
  .page-code { position: absolute; left: 1136px; top: 129px; font-size: 12px; color: #e6f5fc; }
</style>
</head>
<body>
  <header class="site-header">
    <div class="brand">
      <span class="brand-mark"></span>
      <div>
        <div class="brand-name">TALKSIFT</div>
        <div class="brand-tagline">Bring Resumes to Life</div>
      </div>
    </div>
    <a class="header-button login">Login</a>
    <a class="header-button signup">Create Account</a>
  </header>

  <nav class="main-nav">
    <a class="nav-tab active">Benefits</a>
    <a class="nav-tab pricing">Pricing</a>
  </nav>

  <main>
    <h1 class="page-title">Create an Account For FREE!</h1>

    <h2 class="section-title personal">Personal Information</h2>
    <div class="field col-left" style="top:267px">Firstname</div>
    <div class="field col-left" style="top:318px">Lastname</div>
    <div class="field col-left" style="top:369px">Email Address</div>
    <div class="field col-left" style="top:420px">Password</div>
    <span class="help-dot" style="left:431px;top:436px">?</span>
    <div class="field col-left" style="top:471px">Retype Password</div>

    <div class="captcha">
      <div class="captcha-images">
        <div class="captcha-word" role="img" aria-label="Distorted verification number"></div>
        <div class="captcha-photo" role="img" aria-label="Photo of a house number to verify"></div>
      </div>
      <div class="captcha-controls"><span></span><span></span><span></span></div>
      <div class="captcha-badge"><i></i>SAFECHECK</div>
      <div class="captcha-input">Type the text</div>
      <a class="captcha-link">Privacy &amp; Terms</a>
    </div>

    <h2 class="section-title company">Company Information</h2>
    <span class="help-dot" style="left:858px;top:231px">?</span>
    <div class="field col-right" style="top:267px">Company Name</div>
    <div class="field col-right" style="top:318px">Company Address1</div>
    <div class="field col-right" style="top:369px">Company Address2</div>
    <div class="field col-right" style="top:420px">Company City</div>
    <span class="state-label">State</span>
    <div class="state-select">AL
      <svg width="10" height="16" viewBox="0 0 10 16"><path d="M1 6 L5 1 L9 6 Z M1 10 L5 15 L9 10 Z" fill="#888"/></svg>
    </div>
    <div class="field col-right" style="top:522px">Company Zip Code</div>
    <div class="field col-right" style="top:573px">Company Phone Number</div>
    <div class="field col-right" style="top:624px">Company Website</div>
    <a class="submit-button">Create Account</a>
  </main>

  <footer class="site-footer">
    <div class="footer-heading footer-value">The TalkSift Value
      <p>TalkSift video interviewing makes prescreening potential employees quick, safe, and extremely easy. With no contracts, hidden fees, or complicated user interfaces, we make video screening / interviewing a snap.</p>
    </div>
    <span class="footer-divider" style="left:588px"></span>
    <div class="footer-heading footer-contact">Contact Us
      <ul>
        <li>E | info@talksift.com</li>
        <li>Privacy Policy</li>
        <li>Terms and Conditions</li>
      </ul>
    </div>
    <span class="footer-divider" style="left:793px"></span>
    <div class="footer-heading footer-follow">Follow us on</div>
    <div class="social-links">
      <span role="img" aria-label="Social network link"></span>
      <span role="img" aria-label="Social network link"></span>
      <span role="img" aria-label="Social network link"></span>
    </div>
    <span class="page-code">M1</span>
  </footer>
</body>
</html>
```